Harborview Estates Business Card for Apartment Buildings

Create business cards for resident managers who run apartment buildings. The audience is the public who are searching for apartment rentals, and current residents who live at the apartment building. Key design element will be incorporating the company logo, however, the logo cannot dominate. The building name and manager name are more important than the logo. Current business card design leaves little room for copy, so we may need to reduce the size on the current card to allow for more space for copy.

Target Market(s)

Adults 18-65 years of age, who are looking for an apartment rental, plus current residents who live at our apartment buildings.

Industry/Entity Type

Property Management

Contact Information for Business Card

A major design element will be use of the company logo. Important property and manager contact information must be part of the design. The size of the logo will need to be reduced to make room for building and manager contact copy.

Font styles to use
Sans Serif

Colors
3176b5
000000
959595
ffffff

Requirements
Must have
• 1) Incorporate the company logo.
• 2) Use the company colors (dark blue, black/grey, over white).
• 3) FEATURE THE BUILDING NAME
• 4) FEATURE THE MANAGER NAME
• 5) The company name is less important than BUILDING and MANAGER
• 6) Manager contact information
• **SEE ATTACHED CREATIVE BRIEF**
Nice to have
• 1) Back of card logo watermark
• 2) Ability to write notes on back of carfd
Should not have
• Avoid letting the company logo dominate the card, the building name and manager are more important than the company logo.

```html
<!DOCTYPE html>
<html lang="en">
<head>
<meta charset="utf-8">
<title>Harborview Estates Business Card</title>
<link href="https://fonts.googleapis.com/css2?family=Arimo:wght@400;700&display=swap" rel="stylesheet">
<style>
  :root {
    --brand-blue: #1a6fb0;
    --ink: #222222;
    --band-grey: #474747;
    --mid-grey: #959595;
    --paper: #ffffff;
    --backdrop: #e9e9e9;
  }
  html, body {
    margin: 0;
    width: 1200px;
    height: 1200px;
    overflow: hidden;
    background: var(--backdrop);
    font-family: "Arimo", Arial, sans-serif;
  }
  .card {
    position: absolute;
    left: 180px;
    width: 840px;
    height: 480px;
    background: var(--paper);
    box-shadow: 0 6px 18px rgba(0,0,0,0.15);
    overflow: hidden;
  }
  .card--back { top: 90px; }
  .card--front { top: 630px; }

  .company-name {
    margin: 0;
    color: var(--brand-blue);
    font-weight: 700;
    letter-spacing: 0.5px;
    display: flex;
    align-items: center;
    gap: 10px;
    white-space: nowrap;
  }
  .company-name .dot {
    width: 22px;
    height: 22px;
    border-radius: 50%;
    background: var(--brand-blue);
    flex: none;
  }

  /* Front */
  .card--front .company-name {
    position: absolute;
    left: 40px;
    top: 120px;
    font-size: 30px;
  }
  .contact-block {
    position: absolute;
    left: 470px;
    top: 60px;
    color: var(--ink);
  }
  .manager-name {
    margin: 0;
    font-size: 36px;
    font-weight: 700;
    color: var(--brand-blue);
  }
  .manager-title {
    margin: 2px 0 0;
    font-size: 14px;
    color: var(--ink);
  }
  .building-name {
    margin: 22px 0 2px;
    font-size: 24px;
    font-weight: 700;
    color: var(--brand-blue);
  }
  .address {
    margin: 0;
    font-size: 19px;
    line-height: 1.25;
    font-style: normal;
  }
  .contact-list {
    list-style: none;
    margin: 14px 0 0;
    padding: 0;
    font-size: 19px;
    line-height: 1.3;
  }
  .contact-list li {
    display: flex;
    align-items: center;
    gap: 10px;
  }
  .contact-list svg {
    width: 16px;
    height: 16px;
    fill: var(--ink);
    flex: none;
  }
  .band-grey {
    position: absolute;
    left: 0;
    bottom: 0;
    width: 490px;
    height: 22px;
    background: var(--band-grey);
  }
  .band-blue {
    position: absolute;
    left: 490px;
    right: 0;
    bottom: 0;
    height: 44px;
    background: var(--brand-blue);
    color: var(--paper);
    font-size: 20px;
    display: flex;
    align-items: center;
    padding-left: 40px;
  }
  .band-mark {
    position: absolute;
    left: 472px;
    bottom: 8px;
    width: 36px;
    height: 36px;
    border-radius: 50%;
    background: var(--paper);
    border: 4px solid var(--brand-blue);
    box-sizing: border-box;
  }

  /* Back */
  .card--back .back-sign {
    position: absolute;
    right: 40px;
    bottom: 40px;
    text-align: right;
  }
  .card--back .company-name {
    font-size: 22px;
    justify-content: flex-end;
  }
  .card--back .company-name .dot { width: 16px; height: 16px; }
  .card--back .web {
    margin: 6px 0 0;
    font-size: 15px;
    color: var(--brand-blue);
    letter-spacing: 1px;
  }
</style>
</head>
<body>

<section class="card card--back" aria-label="Card back">
  <div class="back-sign">
    <p class="company-name"><span class="dot"></span>Harborview Estates</p>
    <p class="web">www.harborviewest.com</p>
  </div>
</section>

<section class="card card--front" aria-label="Card front">
  <p class="company-name"><span class="dot"></span>Harborview Estates</p>

  <div class="contact-block">
    <h1 class="manager-name">Marisol Delgado</h1>
    <p class="manager-title">Resident Manager</p>
    <h2 class="building-name">Cedar Ridge Apartments</h2>
    <address class="address">2185 Linden Avenue<br>Fairview, CA 90210</address>
    <ul class="contact-list">
      <li>
        <svg viewBox="0 0 16 16" aria-hidden="true"><path d="M3 1h3l1 4-2 1c1 2 3 4 5 5l1-2 4 1v3c0 1-1 2-2 2C7 15 1 9 1 3c0-1 1-2 2-2z"/></svg>
        555-310-4821
      </li>
      <li>
        <svg viewBox="0 0 16 16" aria-hidden="true"><path d="M4 0h8a1 1 0 0 1 1 1v14a1 1 0 0 1-1 1H4a1 1 0 0 1-1-1V1a1 1 0 0 1 1-1zm1 2v10h6V2z"/></svg>
        555-472-9035
      </li>
      <li>
        <svg viewBox="0 0 16 16" aria-hidden="true"><path d="M4 1h6v4H4zM1 6h14v7h-3v2H4v-2H1zm4 5v2h6v-2z"/></svg>
        555-608-1174
      </li>
      <li>
        <svg viewBox="0 0 16 16" aria-hidden="true"><path d="M1 3h14v10H1zm1 1v1l6 4 6-4V4z"/></svg>
        marisol@harborviewest.com
      </li>
    </ul>
  </div>

  <div class="band-grey"></div>
  <div class="band-blue">www.harborviewest.com</div>
  <div class="band-mark"></div>
</section>

</body>
</html>
```